Birchline Septic Solutions

Would like to see some single sided ones but would also like to see some double sided with one sided only being the logo. Owners name is Colin Vandro. Phone number is 555-214-0387
Services are pumping, inspections, installs, and repairs

Contact Information for Business Card

555-241-0387 Colin Vandro Maplecrest, OH

```html
<!DOCTYPE html>
<html lang="en">
<head>
<meta charset="utf-8">
<title>Birchline Septic Solutions – Business Card</title>
<link href="https://fonts.googleapis.com/css2?family=Montserrat:wght@400;700;800&display=swap" rel="stylesheet">
<style>
  :root {
    --backdrop: #4a4a4a;
    --card-black: #161616;
    --teal: #2bbdb8;
    --white: #ffffff;
    --card-w: 560px;
    --card-h: 320px;
  }
  * { box-sizing: border-box; margin: 0; padding: 0; }
  html, body {
    width: 1200px; height: 801px; overflow: hidden;
    background: var(--backdrop);
    font-family: "Montserrat", Arial, sans-serif;
  }
  .stage {
    position: relative; width: 1200px; height: 801px;
    display: flex; align-items: center; justify-content: center; gap: 40px;
  }
  .card {
    position: relative; width: var(--card-w); height: var(--card-h);
    background: var(--card-black); overflow: hidden;
    box-shadow: 0 10px 30px rgba(0,0,0,.35);
  }
  .card__wave { position: absolute; inset: 0; }

  /* Wordmark */
  .wordmark {
    position: absolute; color: var(--white); font-weight: 800;
    display: flex; flex-direction: column; align-items: flex-start;
  }
  .wordmark__name { line-height: 1; letter-spacing: .02em; }
  .wordmark__sub { letter-spacing: .28em; line-height: 1; margin-top: 8px; }
  .wordmark__square { position: absolute; background: var(--teal); }

  .card--contact .wordmark { left: 28px; top: 128px; }
  .card--contact .wordmark__name { font-size: 30px; }
  .card--contact .wordmark__sub { font-size: 11px; }
  .card--contact .wordmark__square { width: 12px; height: 12px; left: 0; top: -22px; }

  .divider {
    position: absolute; left: 248px; top: 60px; width: 2px; height: 170px;
    background: var(--teal);
  }
  .contact { position: absolute; left: 268px; top: 40px; color: var(--white); }
  .contact__name { color: var(--teal); font-weight: 700; font-size: 24px; line-height: 1.1; }
  .contact__place { font-size: 12px; margin-top: 2px; }
  .contact__list { list-style: none; margin-top: 18px; }
  .contact__item {
    display: flex; align-items: center; gap: 8px;
    font-size: 13px; line-height: 1.55;
  }
  .contact__icon { width: 11px; height: 11px; flex: none; }
  .contact__address { font-size: 13px; line-height: 1.4; margin-top: 14px; }

  .card--logo .wordmark { left: 0; right: 0; top: 92px; align-items: center; }
  .card--logo .wordmark__name { font-size: 58px; }
  .card--logo .wordmark__sub { font-size: 18px; margin-top: 12px; }
  .card--logo .wordmark__square { width: 16px; height: 16px; left: 72px; top: 22px; }

  .services-band {
    position: absolute; left: 0; right: 0; top: 248px; height: 32px;
    background: var(--teal); color: var(--white);
    font-size: 17px; display: flex; align-items: center; justify-content: center;
  }
</style>
</head>
<body>
<main class="stage">

  <section class="card card--contact" aria-label="Business card, contact side">
    <svg class="card__wave" viewBox="0 0 560 320" aria-hidden="true">
      <path d="M190 320 C320 300 390 240 440 180 C490 120 520 100 560 95 L560 320 Z" fill="var(--teal)"/>
      <path d="M215 300 C330 285 395 215 440 160 C485 105 515 82 548 78 C515 92 488 118 448 168 C400 228 335 288 215 300 Z" fill="var(--white)"/>
    </svg>

    <div class="wordmark">
      <span class="wordmark__square"></span>
      <span class="wordmark__name">BIRCHLINE</span>
      <span class="wordmark__sub">SEPTIC SOLUTIONS</span>
    </div>

    <div class="divider"></div>

    <div class="contact">
      <p class="contact__name">Colin Vandro</p>
      <p class="contact__place">Maplecrest</p>
      <ul class="contact__list">
        <li class="contact__item">
          <svg class="contact__icon" viewBox="0 0 12 12"><path d="M2.5 1 L4.5 1 L5.3 3.4 L4 4.4 C4.7 5.9 6 7.2 7.6 8 L8.6 6.7 L11 7.5 L11 9.5 C11 10.3 10.3 11 9.5 11 C4.8 11 1 7.2 1 2.5 C1 1.7 1.7 1 2.5 1 Z" fill="var(--teal)"/></svg>
          555-214-0387
        </li>
        <li class="contact__item">
          <svg class="contact__icon" viewBox="0 0 12 12"><rect x="0.5" y="2" width="11" height="8" fill="var(--teal)"/><path d="M0.5 2 L6 6.5 L11.5 2" stroke="var(--card-black)" stroke-width="1" fill="none"/></svg>
          info@youremail.com
        </li>
        <li class="contact__item">
          <svg class="contact__icon" viewBox="0 0 12 12"><circle cx="6" cy="6" r="5.5" fill="var(--teal)"/><path d="M0.5 6 H11.5 M6 0.5 C3.5 3 3.5 9 6 11.5 M6 0.5 C8.5 3 8.5 9 6 11.5" stroke="var(--card-black)" stroke-width=".8" fill="none"/></svg>
          www.yourwebsite.com
        </li>
      </ul>
      <p class="contact__address">Your address, City<br>State, Zip 1234</p>
    </div>
  </section>

  <section class="card card--logo" aria-label="Business card, logo side">
    <div class="wordmark">
      <span class="wordmark__square"></span>
      <span class="wordmark__name">BIRCHLINE</span>
      <span class="wordmark__sub">SEPTIC SOLUTIONS</span>
    </div>
    <p class="services-band">Services are pumping, inspections, installs, and repairs</p>
  </section>

</main>
</body>
</html>
```